SkyvornQ Business Cards and Stationary Design

Need a design for our business cards and stationary. I want to carry on the theme of the logo. I want the business cards to have a design on the back. I would like the business cards and the stationary to carry the same theme, design scheme, and branding

Target Market(s)

Airlines and Maintenance Facilities

Industry/Entity Type

Aviation

Contact Information for Business Card

Name
Position Title
Address: 4827 Trellis Hollow Road, Brinmoor Bay, Calveria 51093
Office Number
Mobile Number
Email
Website

Font styles to use
Serif
Sans Serif

Colors

Designer to choose colors to be used in the design.

```html
<!DOCTYPE html>
<html lang="en">
<head>
<meta charset="utf-8">
<title>SkyvornQ Business Card</title>
<link href="https://fonts.googleapis.com/css2?family=Roboto:wght@400;500&family=Montserrat:wght@700&display=swap" rel="stylesheet">
<style>
  :root {
    --backdrop: #d8d1c7;
    --navy-deep: #141e30;
    --navy-mid: #253753;
    --navy-edge: #1c4f8f;
    --frost-light: #eef1f3;
    --frost-shade: #cfd6dc;
    --accent-blue: #3592e6;
    --text-light: #e6ebf2;
    --text-soft: #c7d0dc;
    --wordmark: #142238;
  }
  * { margin: 0; padding: 0; box-sizing: border-box; }
  html, body {
    width: 1200px; height: 969px; overflow: hidden;
    background: var(--backdrop);
  }
  .business-card {
    position: absolute;
    left: 188px; top: 248px;
    width: 872px; height: 494px;
    border-radius: 26px;
    overflow: hidden;
    background: linear-gradient(150deg, var(--frost-light), var(--frost-shade));
    box-shadow: 0 18px 40px rgba(40, 30, 20, 0.22);
    font-family: "Roboto", sans-serif;
  }
  .card-panel { position: absolute; inset: 0; width: 100%; height: 100%; }
  .contact-block { position: absolute; left: 60px; top: 70px; color: var(--text-light); }
  .person-name {
    font-size: 32px; font-weight: 500; letter-spacing: 1px;
    color: var(--accent-blue); line-height: 1;
  }
  .person-title { margin-top: 8px; font-size: 20px; letter-spacing: 0.5px; color: var(--text-light); }
  .address { position: absolute; left: 60px; top: 255px; font-size: 21px; line-height: 28px; color: var(--text-soft); }
  .contact-list { position: absolute; left: 60px; top: 328px; list-style: none; }
  .contact-list li {
    display: flex; align-items: center; gap: 12px;
    font-size: 20px; line-height: 27px; color: var(--text-soft);
  }
  .contact-list svg { width: 16px; height: 16px; fill: var(--accent-blue); flex: none; }
  .brand {
    position: absolute; left: 420px; top: 158px; width: 400px;
    display: flex; flex-direction: column; align-items: center; gap: 22px;
  }
  .brand-dot {
    width: 96px; height: 96px; border-radius: 50%;
    border: 10px solid var(--wordmark);
  }
  .brand-name {
    font-family: "Montserrat", sans-serif; font-weight: 700;
    font-size: 44px; letter-spacing: 5px; color: var(--wordmark);
  }
</style>
</head>
<body>
  <div class="business-card">
    <svg class="card-panel" viewBox="0 0 872 494" preserveAspectRatio="none" aria-hidden="true">
      <defs>
        <linearGradient id="panelFill" x1="0" y1="0" x2="1" y2="1">
          <stop offset="0" stop-color="#253753"/>
          <stop offset="0.6" stop-color="#1a2740"/>
          <stop offset="1" stop-color="#141e30"/>
        </linearGradient>
      </defs>
      <path d="M0 0 H560 C430 90 390 400 520 494 H0 Z" fill="url(#panelFill)"/>
      <path d="M560 0 C430 90 390 400 520 494" fill="none" stroke="#1c4f8f" stroke-width="8"/>
    </svg>

    <div class="contact-block">
      <p class="person-name">MARCUS DELANE</p>
      <p class="person-title">CEO/FOUNDER</p>
    </div>

    <p class="address">4827 Trellis Hollow Road<br>Brinmoor Bay, Calveria 51093</p>

    <ul class="contact-list">
      <li><svg viewBox="0 0 16 16"><path d="M3.5 1l2.5 3-1.5 2c1 2 3 4 5 5l2-1.5 3 2.5-1.5 2.5C7 14 2 9 1 2.5z"/></svg>772 415 0386</li>
      <li><svg viewBox="0 0 16 16"><path d="M4 0h8v16H4zM5.5 2v10h5V2zM7 13.2h2v1.3H7z" fill-rule="evenodd"/></svg>772 903 5127</li>
      <li><svg viewBox="0 0 16 16"><path d="M0 3h16v1L8 9 0 4zM0 5.5l8 5 8-5V13H0z"/></svg>info@skyvornq.com</li>
      <li><svg viewBox="0 0 16 16"><path d="M8 0a8 8 0 100 16A8 8 0 008 0zm0 1.5c.9 1.2 1.5 2.8 1.7 5.5H6.3C6.5 4.3 7.1 2.7 8 1.5zM1.6 9h3.2c.1 2 .6 3.8 1.3 5.2A6.5 6.5 0 011.6 9zm4.7 0h3.4c-.2 2.5-.8 4.1-1.7 5.5-.9-1.4-1.5-3-1.7-5.5zm4.9 0h3.2a6.5 6.5 0 01-4.5 5.2c.7-1.4 1.2-3.2 1.3-5.2zM1.6 7a6.5 6.5 0 014.5-5.2C5.4 3.2 4.9 5 4.8 7zm9.6 0c-.1-2-.6-3.8-1.3-5.2A6.5 6.5 0 0114.4 7z"/></svg>www.skyvornq.com</li>
    </ul>

    <div class="brand">
      <div class="brand-dot"></div>
      <p class="brand-name">SKYVORNQ</p>
    </div>
  </div>
</body>
</html>
```